Presentation Of Our Epidemiology Consulting Framework

We need a slide deck (png files) for PowerPoint that describes our organization and type of clients we serve, and our 6 phase framework that explains how we work with clients. Please use the minimum amount of text on each slide.  We want a more visual display of how to work with us. We want it to look very similar to our brochure.  We want to also have a few extra branded slides without text that can be used as a template if we decide to add to the deck later or create a new slide deck.
Colors
#56588C
#F28444
#F2E088
#F24C27
#ODODOD

```html
<!DOCTYPE html>
<html lang="en">
<head>
<meta charset="utf-8">
<title>DrVarnell Framework – Slide Deck</title>
<link rel="stylesheet" href="https://fonts.googleapis.com/css2?family=Bebas+Neue&family=Montserrat:ital,wght@0,400;0,500;0,700;1,400&family=Great+Vibes&display=swap">
<style>
  :root{
    --navy-deep:#1c1a4a;
    --navy:#2b2a62;
    --indigo:#56588C;
    --indigo-soft:#4a4a88;
    --orange:#F0732F;
    --orange-soft:#F28444;
    --ink:#0D0D0D;
    --text:#3c3c4a;
    --muted:#6b6b78;
    --rule:#e6e6ee;
    --page:#e2e2e4;
    --white:#ffffff;
  }
  *{box-sizing:border-box;margin:0;padding:0}
  html,body{width:1031px;height:1200px;overflow:hidden;background:var(--page)}
  body{position:relative;font-family:"Montserrat",sans-serif;color:var(--text)}

  .slide{position:absolute;width:765px;height:430px;background:var(--white);overflow:hidden;
    transform:scale(0.579);transform-origin:0 0;box-shadow:0 2px 6px rgba(0,0,0,.08)}
  .col-left{left:40px}.col-right{left:537px}
  .row-1{top:43px}.row-2{top:329px}.row-3{top:614px}.row-4{top:899px}

  .band{position:absolute;left:0;top:0;width:765px;height:55px;border-bottom-right-radius:55px 55px;
    background:linear-gradient(90deg,var(--navy-deep),var(--navy) 55%,var(--indigo-soft))}
  .band-title{position:absolute;left:33px;top:13px;font-family:"Bebas Neue",sans-serif;font-size:25px;
    letter-spacing:.3px;color:var(--white);line-height:1}

  .foot-rule{position:absolute;left:33px;right:34px;top:386px;height:1px;background:var(--rule)}
  .logo{position:absolute;display:flex;align-items:center;gap:5px;font-weight:700;font-size:19px;color:#3a3878;letter-spacing:-.3px}
  .logo-dot{width:14px;height:14px;border-radius:50%;background:var(--orange)}
  .logo-foot{left:33px;top:398px}
  .pageno{position:absolute;left:708px;top:398px;width:23px;height:23px;border-radius:3px;background:var(--orange);
    color:var(--white);font-size:9.5px;font-weight:700;display:flex;align-items:center;justify-content:center}

  .photo{position:absolute}
  .heading{position:absolute;font-size:14px;font-weight:500;color:var(--ink)}
  .checklist{position:absolute;list-style:none}
  .checklist li{position:relative;padding-left:24px;font-size:10.5px;line-height:20px;color:var(--muted)}
  .checklist li::before{content:"";position:absolute;left:1px;top:5px;width:11px;height:11px;border:1.4px solid var(--orange);border-radius:50%}
  .checklist li::after{content:"";position:absolute;left:5px;top:6px;width:4px;height:7px;border:solid var(--navy);border-width:0 1.6px 1.6px 0;transform:rotate(40deg)}
  .checklist.small li{font-size:9.5px}

  .card{position:absolute;background:var(--white);border-radius:8px;box-shadow:0 3px 14px rgba(40,40,90,.12)}
  .icon-badge{position:absolute;width:66px;height:66px;border-radius:50%;background:var(--orange);
    border:4px solid #fde3d3;display:flex;align-items:center;justify-content:center}
  .dotline{position:absolute;height:6px}
  .dotline::before{content:"";position:absolute;left:4px;right:4px;top:2px;border-top:1px dashed #9a9aae}
  .dotline i{position:absolute;top:0;width:6px;height:6px;border-radius:50%;background:var(--orange)}
  .dotline i:first-child{left:0}.dotline i:last-child{right:0}

  /* slide 1 */
  .cover-bg{position:absolute;inset:0;background:linear-gradient(120deg,#2a2a6c,#3a3c90 45%,#4546a0)}
  .cover-shape{position:absolute;inset:0}
  .logo-top{right:33px;top:17px}
  .tagline{position:absolute;left:416px;top:140px;font-family:"Great Vibes",cursive;font-size:15px;color:var(--navy)}
  .cover-title{position:absolute;left:416px;top:162px;font-family:"Bebas Neue",sans-serif;font-size:30px;color:var(--ink);line-height:1}
  .cover-text{position:absolute;left:416px;top:213px;width:325px;font-size:10.8px;line-height:20px;color:var(--ink)}
  .cover-btn{position:absolute;left:419px;top:316px;width:209px;height:30px;border-radius:15px;background:var(--orange);
    color:var(--white);font-size:9px;font-weight:700;display:flex;align-items:center;justify-content:center;gap:5px}

  /* slide 4 */
  .hero-dark{position:absolute;left:0;top:0;width:765px;height:285px;border-radius:0 0 55px 55px;
    background:linear-gradient(90deg,#1e1c4e,#2d2c66 50%,#45468a)}
  .hero-title{position:absolute;left:0;right:0;top:20px;text-align:center;font-family:"Bebas Neue",sans-serif;font-size:26px;color:var(--white)}
  .hero-sub{position:absolute;left:0;right:0;top:62px;text-align:center;font-size:13px;color:var(--white)}
  .hero-note{position:absolute;left:0;right:0;top:92px;text-align:center;font-size:11px;font-style:italic;color:#e4e4f2}
  .service{position:absolute;top:218px;width:138px;height:134px;text-align:center}
  .service svg{margin-top:20px}
  .service p,.deliv p{font-size:9.8px;line-height:17px;color:var(--muted);margin-top:8px}

  .deliv{position:absolute;width:116px;height:106px;text-align:center}
  .deliv svg{margin-top:14px}
</style>
</head>
<body>

<!-- 01 Cover -->
<section class="slide col-left row-1">
  <div class="cover-bg photo" role="img" aria-label="Photo of two scientists in lab coats working in a laboratory"></div>
  <svg class="cover-shape" viewBox="0 0 765 430" width="765" height="430">
    <path d="M505,0 C392,80 318,200 330,300 C340,370 388,410 430,430 L765,430 L765,0 Z" fill="#F0732F"/>
    <path d="M518,0 C408,82 336,200 348,298 C357,366 402,408 448,430 L765,430 L765,0 Z" fill="#ffffff"/>
  </svg>
  <div class="logo logo-top"><span class="logo-dot"></span>DrVarnell</div>
  <p class="tagline">Transforming Health Data Into community Impact</p>
  <h1 class="cover-title">THE DR.VARNELL FRAMEWORK</h1>
  <p class="cover-text">DrVarnell LLC is an epidemiology consulting firm that supports large nonprofit organizations and government agencies that serve black, indigenous, and people of color commonly referred to as BIPOC communities.</p>
  <div class="cover-btn">
    <svg width="9" height="7" viewBox="0 0 9 7"><rect x=".5" y=".5" width="8" height="6" fill="#fff"/><path d="M.5 .5 L4.5 4 L8.5 .5" stroke="#F0732F" fill="none"/></svg>
    SUPPORT@DRVARNELL.COM
  </div>
</section>

<!-- 02 Discovery -->
<section class="slide col-right row-1">
  <div class="band"></div><h2 class="band-title">DISCOVERY &amp; VISION ALIGNMENT</h2>
  <h3 class="heading" style="left:33px;top:138px">Building The Foundation For Success</h3>
  <ul class="checklist" style="left:33px;top:170px;width:250px">
    <li>Deep-dive exploration of your organization's unique challenges and opportunities</li>
    <li style="margin-top:6px">Strategic alignment of goals and expectations</li>
    <li style="margin-top:6px">Custom-tailored solution design</li>
    <li style="margin-top:6px">Clear roadmap development with defined milestones</li>
  </ul>
  <div class="photo" style="left:382px;top:93px;width:342px;height:274px;background:var(--orange);border-top-right-radius:40px;border-bottom-left-radius:30px"></div>
  <div class="photo" role="img" aria-label="Photo of two medical staff in masks and lab coats on a staircase"
       style="left:382px;top:93px;width:336px;height:268px;border-top-right-radius:36px;border-bottom-left-radius:28px;background:linear-gradient(135deg,#c9ccd6,#8e93a6 55%,#5c5d74)"></div>
  <div class="foot-rule"></div>
  <div class="logo logo-foot"><span class="logo-dot"></span>DrVarnell</div>
  <div class="pageno">02</div>
</section>

<!-- 03 Partnership -->
<section class="slide col-left row-2">
  <div class="band"></div><h2 class="band-title">PARTNERSHIP LAUNCH</h2>
  <div class="photo" role="img" aria-label="Photo of three doctors meeting at a table with a laptop"
       style="left:35px;top:90px;width:380px;height:264px;border-radius:6px;background:linear-gradient(135deg,#9aa0ad,#d9dbe0 55%,#eef0f3)"></div>
  <div class="card" style="left:456px;top:128px;width:276px;height:220px"></div>
  <div class="icon-badge" style="left:474px;top:96px">
    <svg width="34" height="34" viewBox="0 0 34 34" fill="none" stroke="#fff" stroke-width="1.6"><circle cx="14" cy="19" r="8"/><circle cx="14" cy="19" r="3"/><circle cx="24" cy="10" r="5.5"/><circle cx="24" cy="10" r="2"/></svg>
  </div>
  <h3 class="heading" style="left:474px;top:178px">Setting The Stage For Excellence</h3>
  <ul class="checklist small" style="left:474px;top:205px">
    <li>Formation of dedicated project team</li>
    <li>Establishment of collaborative workflow</li>
    <li>Comprehensive data gathering</li>
    <li>Strategic timeline planning</li>
    <li>Stakeholder engagement and vision capture</li>
  </ul>
  <div class="dotline" style="left:474px;top:318px;width:240px"><i></i><i></i></div>
  <div class="foot-rule"></div>
  <div class="logo logo-foot"><span class="logo-dot"></span>DrVarnell</div>
  <div class="pageno">03</div>
</section>

<!-- 04 Expert Execution -->
<section class="slide col-right row-2">
  <div class="hero-dark" role="img" aria-label="Dark tinted photo of a scientist in a laboratory"></div>
  <h2 class="hero-title">EXPERT EXECUTION</h2>
  <p class="hero-sub">Where Science Meets Service</p>
  <p class="hero-note">Our Specialized Team Begins The Transformation Process</p>
  <div class="card service" style="left:93px">
    <svg width="42" height="40" viewBox="0 0 42 40" fill="none" stroke="#F0732F" stroke-width="1.5"><rect x="6" y="3" width="22" height="30"/><path d="M10 10h8M10 15h14M10 20h10M10 25h8"/><circle cx="28" cy="26" r="6"/><path d="M32 30l6 6"/></svg>
    <p>In-Depth Research<br>and Analysis</p>
  </div>
  <div class="card service" style="left:240px">
    <svg width="42" height="40" viewBox="0 0 42 40" fill="none" stroke="#F0732F" stroke-width="1.5"><path d="M4 36h34M8 36V26h6v10M18 36V20h6v16M28 36V14h6v22"/><path d="M6 20L16 12l6 5 12-12"/><path d="M28 5h6v6"/></svg>
    <p>Content Development<br>&amp; Refinement</p>
  </div>
  <div class="card service" style="left:386px">
    <svg width="42" height="40" viewBox="0 0 42 40" fill="none" stroke="#F0732F" stroke-width="1.5"><circle cx="14" cy="12" r="8"/><circle cx="14" cy="12" r="3"/><circle cx="27" cy="27" r="9"/><circle cx="27" cy="27" r="3.5"/><path d="M6 30h8M6 35h10"/></svg>
    <p>Data Interpretation<br>&amp; Visualization</p>
  </div>
  <div class="card service" style="left:533px">
    <svg width="42" height="40" viewBox="0 0 42 40" fill="none" stroke="#F0732F" stroke-width="1.5"><path d="M21 35C8 26 3 19 3 12a8 8 0 0 1 18-3 8 8 0 0 1 18 3c0 7-5 14-18 23z"/><path d="M6 20h9l3-6 4 10 3-4h10"/></svg>
    <p>Plain Language<br>Translation Of Complex<br>Health Information</p>
  </div>
  <div class="foot-rule"></div>
  <div class="logo logo-foot"><span class="logo-dot"></span>DrVarnell</div>
  <div class="pageno">04</div>
</section>

<!-- 05 Collaborative Refinement -->
<section class="slide col-left row-3">
  <div class="band"></div><h2 class="band-title">COLLABORATIVE REFINEMENT</h2>
  <div class="card" style="left:35px;top:135px;width:276px;height:205px"></div>
  <div class="icon-badge" style="left:53px;top:103px">
    <svg width="34" height="34" viewBox="0 0 34 34" fill="none" stroke="#fff" stroke-width="1.6"><path d="M17 4l10 4v8c0 7-5 11-10 13-5-2-10-6-10-13V8z"/><path d="M12 17l4 4 7-8"/></svg>
  </div>
  <h3 class="heading" style="left:53px;top:185px">Ensuring Perfect Alignment</h3>
  <ul class="checklist small" style="left:53px;top:212px">
    <li>Presentation of initial frameworks</li>
    <li>Interactive feedback sessions</li>
    <li>Draft review and optimization</li>
    <li>Stakeholder input integration</li>
  </ul>
  <div class="dotline" style="left:53px;top:310px;width:238px"><i></i><i></i></div>
  <div class="photo" style="left:345px;top:83px;width:420px;height:280px;background:var(--orange);border-top-left-radius:8px;border-bottom-left-radius:8px"></div>
  <div class="photo" role="img" aria-label="Photo of hands typing on a laptop over overlaid data charts"
       style="left:352px;top:89px;width:381px;height:268px;border-radius:8px;background:linear-gradient(135deg,#e7e8ec,#c8cad2 50%,#b76b78 80%,#e6e6ea)"></div>
  <div class="foot-rule"></div>
  <div class="logo logo-foot"><span class="logo-dot"></span>DrVarnell</div>
  <div class="pageno">05</div>
</section>

<!-- 06 Impact Delivery -->
<section class="slide col-right row-3">
  <div class="band"></div><h2 class="band-title">IMPACT DELIVERY</h2>
  <div class="photo" role="img" aria-label="Photo of a doctor with floating digital health checklists above a laptop"
       style="left:275px;top:77px;width:456px;height:290px;background:linear-gradient(90deg,#f2f3f5,#c7ccd4 40%,#2f7c6a 60%,#8b8f99 85%,#7a5a52)"></div>
  <h3 class="heading" style="left:33px;top:85px">Bringing Vision To Reality</h3>
  <div class="card deliv" style="left:33px;top:122px">
    <svg width="40" height="36" viewBox="0 0 40 36" fill="none" stroke="#F0732F" stroke-width="1.5"><rect x="4" y="6" width="32" height="20"/><path d="M2 6h36M20 26v8M14 34h12"/><circle cx="25" cy="16" r="5"/><path d="M25 11v5h5M8 12h8M8 17h8"/></svg>
    <p>Final Deliverable<br>Presentation</p>
  </div>
  <div class="card deliv" style="left:159px;top:122px">
    <svg width="40" height="36" viewBox="0 0 40 36" fill="none" stroke="#F0732F" stroke-width="1.5"><circle cx="25" cy="11" r="7"/><path d="M22 11l2 2 4-4"/><path d="M3 26h6l6-3h8a2 2 0 0 1 0 4h-6M9 32l16 0 11-8a2 2 0 0 0-3-3l-8 5"/></svg>
    <p>Implementation<br>support</p>
  </div>
  <div class="card deliv" style="left:33px;top:240px">
    <svg width="40" height="36" viewBox="0 0 40 36" fill="none" stroke="#F0732F" stroke-width="1.5"><circle cx="20" cy="18" r="13"/><circle cx="20" cy="18" r="6"/><path d="M20 5v7M20 24v7M7 18h7M26 18h7"/></svg>
    <p>Knowledge Transfer</p>
  </div>
  <div class="card deliv" style="left:159px;top:240px">
    <svg width="40" height="36" viewBox="0 0 40 36" fill="none" stroke="#F0732F" stroke-width="1.5"><path d="M4 30h32M9 30V20h5v10M17 30V14h5v16M25 30V18h5v12"/><path d="M6 14l10-8 6 4 10-8"/><path d="M27 2h5v5"/></svg>
    <p>Impact Measurement<br>Framework</p>
  </div>
  <div class="foot-rule"></div>
  <div class="logo logo-foot"><span class="logo-dot"></span>DrVarnell</div>
  <div class="pageno">06</div>
</section>

<!-- 07 Template -->
<section class="slide col-left row-4">
  <div class="band"></div><h2 class="band-title">TITILE GOES HERE</h2>
  <div class="foot-rule"></div>
  <div class="logo logo-foot"><span class="logo-dot"></span>DrVarnell</div>
  <div class="pageno">07</div>
</section>

<!-- 08 Evolution -->
<section class="slide col-right row-4">
  <div class="band"></div><h2 class="band-title">EVOLUTION &amp; GROWTH</h2>
  <div class="photo" role="img" aria-label="Photo of hands holding a tablet showing medical data dashboards"
       style="left:33px;top:87px;width:345px;height:278px;border-top-right-radius:40px;border-bottom-left-radius:30px;background:linear-gradient(135deg,#1b3558,#3c6a9a 50%,#c9d6e4)"></div>
  <div class="photo" role="img" aria-label="Photo of a medical team reviewing data on several monitors"
       style="left:409px;top:83px;width:288px;height:153px;border-bottom-left-radius:22px;background:linear-gradient(135deg,#5a6070,#9aa3b3 50%,#d6d0c8)"></div>
  <h3 class="heading" style="left:413px;top:257px">Sustaining Long-Term Success</h3>
  <ul class="checklist small" style="left:413px;top:285px">
    <li>Project success celebration</li>
    <li>Future opportunities exploration</li>
    <li>Partnership evolution planning</li>
    <li>Continuous improvement recommendations</li>
  </ul>
  <div class="foot-rule"></div>
  <div class="logo logo-foot"><span class="logo-dot"></span>DrVarnell</div>
  <div class="pageno">08</div>
</section>

</body>
</html>
```